Business Card Design

We need a design for business cards for our company. We have a logo. We teach EMT's and we are based out of Virginia. The information that will need to add would be, name, title, phone number, email, address. On the back of the business card would be "We help you, help others"

Target Market(s)

People that want to become EMT's

Colors

Designer to choose colors to be used in the design.

Requirements
Must have
• company logo

```html
<!DOCTYPE html>
<html lang="en">
<head>
<meta charset="utf-8">
<title>Rescue Ready Academy – Business Card</title>
<link rel="stylesheet" href="https://fonts.googleapis.com/css2?family=Montserrat:wght@400;500;700&display=swap">
<style>
  :root {
    --page: #e4e5e7;
    --card: #1e2a33;
    --accent: #e8234a;
    --muted: #a3aab0;
    --rule: #6d767d;
  }
  * { margin: 0; padding: 0; box-sizing: border-box; }
  html, body { width: 1200px; height: 1021px; overflow: hidden; }
  body {
    background: var(--page);
    font-family: "Montserrat", sans-serif;
    position: relative;
  }
  .card {
    position: absolute;
    left: 250px;
    width: 700px;
    height: 400px;
    background: var(--card);
    border-radius: 3px;
    box-shadow: 0 10px 28px rgba(0,0,0,.25);
    overflow: hidden;
  }
  .card--back { top: 70px; }
  .card--front { top: 530px; }

  /* back */
  .tagline {
    position: absolute;
    left: 0; right: 0; top: 150px;
    text-align: center;
    font-weight: 700;
    text-transform: uppercase;
    line-height: 1.15;
  }
  .tagline__lead { display: block; color: var(--accent); font-size: 36px; letter-spacing: 1px; }
  .tagline__follow { display: block; color: var(--muted); font-size: 28px; letter-spacing: 1.5px; margin-top: 4px; }

  /* front */
  .brand {
    position: absolute;
    left: 40px; top: 42px;
    display: flex; align-items: center; gap: 12px;
  }
  .brand__mark { width: 16px; height: 16px; background: var(--accent); }
  .brand__name {
    color: var(--accent);
    font-weight: 700;
    font-size: 26px;
    letter-spacing: .5px;
    text-transform: uppercase;
  }
  .divider {
    position: absolute;
    left: 40px; right: 110px; top: 205px;
    height: 1px; background: var(--rule);
  }
  .contact {
    position: absolute;
    left: 40px; top: 232px;
    list-style: none;
    color: var(--muted);
    font-size: 17px;
    line-height: 30px;
  }
  .contact li { display: flex; align-items: center; gap: 10px; }
  .contact svg { width: 15px; height: 15px; flex: none; }
  .person {
    position: absolute;
    right: 70px; top: 232px;
    text-align: right;
  }
  .person__name { color: var(--accent); font-weight: 700; font-size: 24px; }
  .person__title { color: var(--muted); font-size: 18px; margin-top: 2px; }
  .address {
    position: absolute;
    right: 70px; top: 320px;
    color: var(--muted);
    font-size: 17px;
    line-height: 26px;
    text-align: right;
  }
  .edge-bar {
    position: absolute;
    right: 0; top: 236px;
    width: 26px; height: 56px;
    background: var(--accent);
  }
</style>
</head>
<body>
  <section class="card card--back" aria-label="Card back">
    <p class="tagline">
      <span class="tagline__lead">We help you,</span>
      <span class="tagline__follow">Help others</span>
    </p>
  </section>

  <section class="card card--front" aria-label="Card front">
    <div class="brand">
      <span class="brand__mark"></span>
      <span class="brand__name">Rescue Ready Academy</span>
    </div>

    <div class="divider"></div>

    <ul class="contact">
      <li>
        <svg viewBox="0 0 24 24" fill="var(--accent)"><path d="M6.6 10.8a15.1 15.1 0 0 0 6.6 6.6l2.2-2.2a1 1 0 0 1 1-.25 11.4 11.4 0 0 0 3.6.6 1 1 0 0 1 1 1V20a1 1 0 0 1-1 1A17 17 0 0 1 3 4a1 1 0 0 1 1-1h3.5a1 1 0 0 1 1 1c0 1.25.2 2.45.6 3.6a1 1 0 0 1-.25 1z"/></svg>
        (555) 014-2837
      </li>
      <li>
        <svg viewBox="0 0 24 24" fill="none" stroke="var(--accent)" stroke-width="2"><rect x="3" y="5" width="18" height="14"/><path d="M3 5l9 8 9-8"/></svg>
        daniel@rescueready.com
      </li>
      <li>
        <svg viewBox="0 0 24 24" fill="none" stroke="var(--accent)" stroke-width="2"><circle cx="12" cy="12" r="9"/><path d="M3 12h18M12 3c3 3 3 15 0 18M12 3c-3 3-3 15 0 18"/></svg>
        www.rescueready.com
      </li>
    </ul>

    <div class="person">
      <p class="person__name">Daniel Carter</p>
      <p class="person__title">Founder</p>
    </div>

    <p class="address">480 Harbor Lane<br>Norfolk, Virginia, 23510</p>

    <div class="edge-bar"></div>
  </section>
</body>
</html>
```